Business card por a urban DJ, up scale audience target

Need a sober design, modern, conservative colors but i can consider some options, y play rnb, hip hop, EDM and top40.

Business card for contact and personal info, double sided, use logo attrached please; im 42 so i need a card acording to my age an target audience.

Target Market(s)

Adult people, up scale audience

Industry/Entity Type

Music Download

Contact Information for Business Card

Cel (318) 4207265518 www.lumadrift.com

Requirements
Must have
• open mind
Nice to have
• open mind
Should not have
• DJ

```html
<!DOCTYPE html>
<html lang="en">
<head>
<meta charset="utf-8">
<title>Luma business card</title>
<link href="https://fonts.googleapis.com/css2?family=Open+Sans:wght@400;600;800&display=swap" rel="stylesheet">
<style>
  :root {
    --stage: #2a2a2a;
    --paper: #ffffff;
    --ink: #2b2b2b;
    --grey: #a3a3a3;
    --on-dark: #e9e9e9;
  }
  * { margin: 0; padding: 0; box-sizing: border-box; }
  html, body { width: 1200px; height: 1189px; overflow: hidden; }
  body {
    background: var(--stage);
    font-family: "Open Sans", sans-serif;
    position: relative;
  }
  .card {
    position: absolute;
    left: 170px;
    width: 860px;
    height: 490px;
    background: var(--paper);
    overflow: hidden;
  }
  .card--front { top: 80px; }
  .card--back { top: 620px; }
  .card__art { position: absolute; inset: 0; width: 100%; height: 100%; }
  .brand {
    position: absolute;
    font-weight: 800;
    color: var(--ink);
    letter-spacing: 4px;
    line-height: 1;
  }
  .card--front .brand { left: 0; right: 0; top: 110px; text-align: center; font-size: 110px; }
  .front__url {
    position: absolute;
    right: 90px;
    top: 372px;
    color: var(--on-dark);
    font-size: 26px;
  }
  .holder { position: absolute; left: 50px; top: 22px; color: var(--on-dark); }
  .holder__name { font-size: 30px; font-weight: 400; letter-spacing: 1px; line-height: 1.1; }
  .holder__role { font-size: 22px; font-weight: 600; line-height: 1.2; }
  .card--back .brand { left: 50px; top: 185px; font-size: 120px; }
  .contact { position: absolute; right: 60px; top: 150px; width: 300px; text-align: center; color: var(--ink); }
  .contact__item { margin-bottom: 26px; font-size: 24px; }
  .contact__icon { display: block; margin: 0 auto 8px; width: 30px; height: 30px; }
</style>
</head>
<body>
  <section class="card card--front">
    <svg class="card__art" viewBox="0 0 860 490" preserveAspectRatio="none" aria-hidden="true">
      <path fill="var(--grey)" d="M0,430 C180,430 220,300 370,300 L600,300 C690,300 700,250 860,250 L860,490 L0,490 Z"/>
      <path fill="var(--ink)" d="M0,470 C190,470 230,340 380,340 L610,340 C690,340 710,290 860,290 L860,490 L0,490 Z"/>
    </svg>
    <div class="brand">LUMA</div>
    <div class="front__url">www.lumadrift.com</div>
  </section>

  <section class="card card--back">
    <svg class="card__art" viewBox="0 0 860 490" preserveAspectRatio="none" aria-hidden="true">
      <path fill="var(--grey)" d="M0,0 H860 V72 H560 C500,72 490,120 430,120 L0,120 Z"/>
      <path fill="var(--ink)" d="M0,0 H860 V38 H520 C460,38 450,112 390,112 L0,112 Z"/>
      <rect x="0" y="398" width="860" height="14" fill="var(--ink)"/>
      <rect x="0" y="412" width="860" height="78" fill="var(--grey)"/>
    </svg>
    <div class="holder">
      <div class="holder__name">JONATHAN DOE</div>
      <div class="holder__role">Managing Director</div>
    </div>
    <div class="brand">LUMA</div>
    <div class="contact">
      <div class="contact__item">
        <svg class="contact__icon" viewBox="0 0 30 30" aria-hidden="true">
          <circle cx="15" cy="9" r="7" fill="var(--ink)"/>
          <path d="M2,30 C2,20 8,17 15,17 C22,17 28,20 28,30 Z" fill="var(--ink)"/>
        </svg>
        (318) 4207265518
      </div>
      <div class="contact__item">
        <svg class="contact__icon" viewBox="0 0 30 30" aria-hidden="true">
          <circle cx="15" cy="15" r="13" fill="var(--ink)"/>
          <path d="M2,15 H28 M15,2 V28 M6,7 C12,11 18,11 24,7 M6,23 C12,19 18,19 24,23" stroke="var(--paper)" stroke-width="1.5" fill="none"/>
        </svg>
        www.lumadrift.com
      </div>
    </div>
  </section>
</body>
</html>
```